TL - business card

Tallow Partners is an insurance brokerage firm, inovative, proactive, vigorous, which aims to become the leader of the insurance brokers in Anfrica. We should like to get some designs which should be avoided also in Gray / Metallic for the Administration and Orange / Blue for the Managers (ike in the picture sent). The Blue / Green logo is not the correct one, but the source of the file. Please adjust the color accordingly for the business cards. 1 / Orange / Blue 2 / Gray / Metallic We want something classic but which is transmitted strenght, inovation, modernity and most of all, rapidity. We want something start-up like, very punchy and catching eye remaining profesional at the same time. Name: Dorian Whitlock Function: Managing Director Address: N ° 17/18 Rua Veloso - R / C 2B Direita - Bairro Mutamba - Luanda Tel: (+244) 947 582 316 Email: dorian.whitlock@tallow-p.example Website: www.tallow-p. example We want classic in the front and creative, colorfull at the back. The cards will be printed in relief, with very high quality of paper.
Insurance Broker
Colors
Designer to choose colors to be used in the design.

```html
<!DOCTYPE html>
<html lang="en">
<head>
<meta charset="utf-8">
<title>Tallow Partners – Business Card</title>
<link rel="stylesheet" href="https://fonts.googleapis.com/css2?family=Exo+2:wght@700&family=Roboto:wght@300;400&display=swap">
<style>
  :root {
    --backdrop: #e6e6e8;
    --card: #252526;
    --orange: #f04e2e;
    --blue: #2aa9e0;
    --light: #c9c9c9;
    --metal: #9a9a9c;
    --rule: #8a8a8a;
  }
  * { box-sizing: border-box; margin: 0; padding: 0; }
  html, body { width: 1200px; height: 801px; overflow: hidden; }
  body {
    background: var(--backdrop);
    font-family: "Roboto", Arial, sans-serif;
    display: flex;
    align-items: center;
    justify-content: center;
    gap: 60px;
  }
  .card {
    position: relative;
    width: 520px;
    height: 297px;
    background: var(--card);
    box-shadow: 0 10px 30px rgba(0,0,0,.25);
  }
  /* front */
  .brand {
    position: absolute;
    top: 46px;
    right: 60px;
    display: flex;
    align-items: center;
    gap: 12px;
  }
  .brand-dot {
    width: 34px; height: 34px;
    border-radius: 50%;
    background: var(--orange);
  }
  .brand-name {
    font-family: "Roboto", Arial, sans-serif;
    font-weight: 400;
    font-size: 24px;
    letter-spacing: 1px;
    color: var(--orange);
    text-transform: uppercase;
  }
  .divider {
    position: absolute;
    left: 40px; right: 40px;
    top: 165px;
    height: 1px;
    background: var(--rule);
  }
  .person {
    position: absolute;
    left: 40px;
    bottom: 142px;
  }
  .person-name {
    font-family: "Exo 2", Arial, sans-serif;
    font-weight: 700;
    font-size: 25px;
    color: var(--blue);
    line-height: 1.05;
  }
  .person-role {
    font-family: "Exo 2", Arial, sans-serif;
    font-weight: 700;
    font-size: 15px;
    color: var(--orange);
  }
  .contacts {
    position: absolute;
    left: 40px;
    top: 180px;
    list-style: none;
    font-size: 13px;
    font-weight: 300;
    color: var(--light);
    line-height: 20px;
  }
  .contacts li { display: flex; align-items: center; gap: 8px; }
  .contacts svg { width: 12px; height: 12px; fill: var(--blue); flex: none; }
  .address {
    position: absolute;
    right: 40px;
    top: 180px;
    text-align: right;
    font-size: 13px;
    font-weight: 300;
    color: var(--light);
    line-height: 20px;
  }
  /* back */
  .card-back {
    display: flex;
    align-items: center;
    justify-content: center;
    gap: 16px;
  }
  .back-dot {
    width: 64px; height: 64px;
    border-radius: 50%;
    background: #3a3a3b;
  }
  .back-name {
    font-family: "Roboto", Arial, sans-serif;
    font-weight: 400;
    font-size: 38px;
    letter-spacing: 1px;
    color: var(--metal);
    text-transform: uppercase;
  }
</style>
</head>
<body>
  <section class="card card-front">
    <div class="brand">
      <span class="brand-dot"></span>
      <span class="brand-name">Tallow Partners</span>
    </div>
    <div class="person">
      <p class="person-name">Dorian Whitlock</p>
      <p class="person-role">Managing Director</p>
    </div>
    <div class="divider"></div>
    <ul class="contacts">
      <li><svg viewBox="0 0 24 24"><path d="M6.6 10.8a15 15 0 0 0 6.6 6.6l2.2-2.2c.3-.3.7-.4 1-.2 1.1.4 2.3.6 3.6.6.6 0 1 .4 1 1V20c0 .6-.4 1-1 1A17 17 0 0 1 3 4c0-.6.4-1 1-1h3.5c.6 0 1 .4 1 1 0 1.3.2 2.5.6 3.6.1.3 0 .7-.2 1z"/></svg>(+244) 947 582 316</li>
      <li><svg viewBox="0 0 24 24"><path d="M2 5h20v14H2zm2 2v.5l8 5 8-5V7l-8 5z"/></svg>dorian.whitlock@tallow-p.example</li>
      <li><svg viewBox="0 0 24 24"><circle cx="12" cy="12" r="10"/></svg>www.tallow-p. example</li>
    </ul>
    <address class="address" style="font-style:normal">
      N ° 17/18 Rua Veloso<br>
      R / C 2B Direita<br>
      Bairro Mutamba, Luanda
    </address>
  </section>

  <section class="card card-back">
    <span class="back-dot"></span>
    <span class="back-name">Tallow Partners</span>
  </section>
</body>
</html>
```